Wedding Videography Wordpress Website Theme

We need a modern and high-end website look for our wedding video and film business. We film weddings all over the United Kingdom and at European destinations so need something to reflect our work. The website should be visually stunning with images and videos being the focal point as this is what our services are.

The current website is www.brunolessway.com so you will be able to see our brand.

My Snapgram is www.instagram.com/brunolesswayfilms so a new design should link in with this idea.

We need the following pages designed by the winning designer

1 - Homepage
2 - Films Index Page
3 - Testimonials
4 - Prices
5 - Reviews
6 - Meet Bruno (About)
7 - Contact
8 - Blog Index
9 - Blog Page

All pages must be consistent so have a similar style.

Pages on menu:
Meet Bruno
Videos
Packages
Testimionials
Journal (Blog)
Contact

We require a responsive look too. Over 90% of our visitors access the website via their mobile devices.

```html
<!DOCTYPE html>
<html lang="en">
<head>
<meta charset="utf-8">
<title>Bruno Lessway Wedding Films</title>
<link href="https://fonts.googleapis.com/css2?family=Questrial&family=Roboto:wght@400;500;700&display=swap" rel="stylesheet">
<style>
:root{
  --gold:#a48d4f;
  --gold-dark:#8c7740;
  --cream:#f6efdd;
  --ink:#222;
  --text:#666;
  --footer:#2a2a2a;
  --white:#fff;
}
*{box-sizing:border-box;margin:0;padding:0}
html,body{width:1200px;height:4241px;overflow:hidden}
body{font-family:"Roboto",Arial,sans-serif;color:var(--text);background:var(--white);position:relative}
.abs{position:absolute}
.heading{font-family:"Questrial",Arial,sans-serif;color:var(--ink);text-transform:uppercase;font-weight:400}
.gold{color:var(--gold)}
.btn{position:absolute;display:flex;align-items:center;justify-content:center;gap:10px;font:700 13px "Roboto",sans-serif;text-transform:uppercase;letter-spacing:.3px;background:var(--gold);color:var(--white);border-radius:3px}
.btn .arrow{width:14px;height:14px;border-radius:50%;background:var(--white);display:inline-flex;align-items:center;justify-content:center}
.btn .arrow::after{content:"";border-left:5px solid var(--gold);border-top:3.5px solid transparent;border-bottom:3.5px solid transparent;margin-left:2px}
.btn.outline{background:var(--white);color:var(--gold);border:2px solid var(--gold)}
.btn.outline .arrow{background:var(--gold)}
.btn.outline .arrow::after{border-left-color:var(--white)}
.play{position:absolute;width:60px;height:60px;border-radius:50%;background:rgba(255,255,255,.85);border:5px solid var(--gold);display:flex;align-items:center;justify-content:center}
.play::after{content:"";border-left:18px solid var(--gold);border-top:11px solid transparent;border-bottom:11px solid transparent;margin-left:5px}
.dots{position:absolute;left:0;width:1200px;display:flex;justify-content:center;gap:4px}
.dots i{width:9px;height:9px;border-radius:50%;background:var(--gold)}
.dots i.off{background:transparent;border:1.5px solid var(--gold)}

/* hero */
.hero{position:absolute;left:0;top:0;width:1200px;height:728px;background:linear-gradient(100deg,#6f6a5e 0%,#4d5243 35%,#2f3a25 65%,#1e2a18 100%)}
.topbar-phone{left:112px;top:28px;display:flex;gap:16px;align-items:center;color:var(--white)}
.icon-circle{width:38px;height:38px;border-radius:50%;background:var(--gold);display:flex;align-items:center;justify-content:center}
.topbar-phone small{display:block;font:700 10px "Roboto",sans-serif}
.topbar-phone strong{font:700 21px "Roboto",sans-serif}
.brand{left:0;width:1200px;top:52px;text-align:center;color:var(--white);font:400 17px "Questrial",sans-serif;letter-spacing:3px}
.socials{right:112px;top:28px;display:flex;gap:10px}
.socials i{width:38px;height:38px;border-radius:50%;background:var(--gold)}
.nav{left:112px;top:110px;width:976px;height:48px;background:var(--white);display:flex;justify-content:center;align-items:center;gap:36px;font:500 13px "Roboto",sans-serif;color:var(--ink)}
.nav .active{color:var(--gold)}
.hero-title{left:556px;top:290px;font-size:54px;line-height:64px;color:var(--white);letter-spacing:1px}
.hero-sub{left:556px;top:494px;font:700 36px "Roboto",sans-serif;color:var(--white)}

/* intro */
.intro h2{left:112px;top:826px;font-size:29px;line-height:39px}
.intro .lead{left:112px;top:917px;font:500 18px "Roboto",sans-serif;color:var(--gold)}
.intro p{left:112px;top:957px;width:448px;font-size:13px;line-height:23px;text-align:justify}
.framed{left:645px;top:823px;width:443px;height:365px;border:3px solid var(--gold);border-radius:14px;padding:6px;background:var(--white)}
.photo{border-radius:10px;overflow:hidden}

/* latest */
.band-latest{left:0;top:1289px;width:1200px;height:316px;background:var(--gold)}
.latest-title{left:0;width:1200px;top:1355px;text-align:center;color:var(--white);font-size:29px}
.video-card{position:absolute;top:1435px;width:465px;height:338px;border-radius:12px;box-shadow:0 4px 14px rgba(0,0,0,.15);overflow:hidden}

/* about */
.about-silhouette{left:0;top:1770px;width:420px;height:518px;background:linear-gradient(90deg,#8d8d8d,rgba(255,255,255,0))}
.about h2{left:100px;width:1000px;top:1922px;text-align:center;font-size:28px;line-height:39px}
.about p{left:112px;width:976px;top:2064px;text-align:center;font-size:15px;line-height:26px}

/* testimonials */
.testi{left:0;top:2288px;width:1200px;height:523px;background:linear-gradient(180deg,#f6f0e0,#ece1c2)}
.testi-title{left:0;width:1200px;top:2355px;text-align:center;font-size:29px}
.t-card{top:2452px;width:476px;height:206px;background:rgba(255,252,244,.95);border-radius:103px;box-shadow:0 4px 16px rgba(0,0,0,.08)}
.t-card .round{position:absolute;left:20px;top:16px;width:176px;height:176px;border-radius:50%}
.t-card h3{position:absolute;left:218px;top:24px;font:700 15px "Roboto",sans-serif;color:var(--ink)}
.t-card p{position:absolute;left:218px;top:52px;width:226px;font-size:11.5px;line-height:19px;text-align:justify}
.t-card .venue{position:absolute;left:218px;top:152px;font:700 11px "Roboto",sans-serif;color:var(--gold);line-height:19px}

/* packages */
.packs-bg{left:0;top:3000px;width:1200px;height:473px;background:linear-gradient(180deg,#fff,#a5a5a5)}
.packs-title{left:0;width:1200px;top:2890px;text-align:center;font-size:29px}
.pack{top:2963px;width:314px;height:387px;background:var(--white);border-radius:14px;box-shadow:0 4px 18px rgba(0,0,0,.15);overflow:hidden}
.pack svg{position:absolute;left:0;top:0}
.pack h3{position:absolute;left:0;width:100%;top:40px;text-align:center;font:500 21px "Roboto",sans-serif;color:var(--white)}
.price{position:absolute;left:50%;margin-left:-36px;top:82px;width:72px;height:72px;border-radius:50%;background:var(--gold);border:4px solid var(--white);box-shadow:0 0 0 2px var(--gold);color:var(--white);font:700 25px "Roboto",sans-serif;display:flex;align-items:center;justify-content:center}
.pack p{position:absolute;left:18px;width:278px;top:182px;font-size:13px;line-height:22px;text-align:center}

/* contact band */
.touch{left:0;top:3473px;width:1200px;height:346px;background:var(--gold)}
.touch-title{left:0;width:1200px;top:3538px;text-align:center;color:var(--white);font-size:29px}
.touch-text{left:120px;width:960px;top:3604px;text-align:center;color:#f5efe0;font-size:14.5px;line-height:25px}

/* footer */
.footer{left:0;top:3819px;width:1200px;height:422px;background:var(--footer);color:var(--white)}
.f-head{top:3918px;font:700 13px "Roboto",sans-serif;color:var(--white);text-transform:uppercase}
.f-head::after{content:"";display:block;width:40px;height:2px;background:var(--gold);margin-top:6px}
.f-links{left:117px;top:3962px;list-style:none;font-size:13.5px;line-height:31px;color:var(--white)}
.f-links li::before{content:"»";margin-right:14px}
.f-contact{left:388px;top:3960px;font-size:12px;line-height:16px;color:var(--white)}
.f-row{display:flex;gap:16px;align-items:center;margin-bottom:20px}
.f-row .ic{width:34px;height:34px;border-radius:50%;border:1.5px solid #777;display:flex;align-items:center;justify-content:center;flex:none}
.grid{left:643px;top:3950px;display:grid;grid-template-columns:repeat(3,70px);gap:7px}
.grid i{height:55px;background:linear-gradient(135deg,#b98aa8,#6d6a74)}
.copy{left:0;width:1200px;top:4190px;text-align:center;font-size:13px;color:var(--white)}
.f-rule{left:112px;top:4172px;width:976px;height:1px;background:#444}
</style>
</head>
<body>

<!-- Hero -->
<header class="hero" role="img" aria-label="Photo of a bride and groom embracing in front of mountains and a lake"></header>
<div class="abs topbar-phone">
  <span class="icon-circle"><svg width="16" height="16" viewBox="0 0 24 24"><path fill="#fff" d="M6.6 10.8a15 15 0 0 0 6.6 6.6l2.2-2.2c.3-.3.7-.4 1-.2 1.1.4 2.3.6 3.6.6.6 0 1 .4 1 1V20c0 .6-.4 1-1 1A17 17 0 0 1 3 4c0-.6.4-1 1-1h3.5c.6 0 1 .4 1 1 0 1.3.2 2.5.6 3.6.1.3 0 .7-.2 1z"/></svg></span>
  <div><small>CALL US TODAY !</small><strong>07700 900 123</strong></div>
</div>
<div class="abs brand">BRUNO LESSWAY</div>
<div class="abs socials"><i></i><i></i><i></i></div>
<nav class="abs nav">
  <span class="active">HOME</span><span>MEET BRUNO</span><span>VIDEOS</span><span>PACKAGES</span><span>TESTIMONIALS</span><span>JOURNAL (BLOG)</span><span>CONTACT</span>
</nav>
<h1 class="abs heading hero-title">Immortalise your<br>best moments with<br>a beautiful video</h1>
<div class="abs hero-sub">Timeless Wedding Films</div>
<div class="btn" style="left:559px;top:568px;width:152px;height:42px;border:1.5px solid rgba(255,255,255,.5)">Get started <span class="arrow"></span></div>
<div class="play" style="left:740px;top:560px;background:var(--gold);border-color:rgba(255,255,255,.6)"></div>

<!-- Intro -->
<section class="intro">
  <h2 class="abs heading">Your wedding day is the most<br>important day of your life</h2>
  <div class="abs lead">Tell Your Story With A Powerful Video</div>
  <p class="abs">The celebration of your love story… and you'll want to remember it for the rest of your lives.Your wedding film is the best way to keep this day alive forever … a newlywed's gift that keeps giving … an infinite reminder of those special moments and memories.<br>Everything about your wedding day belongs to you, the couple. Your story. Your vibe. Your friends and family. Your pre-wedding jitters. Your tears. Your laughter. Your vows.</p>
  <div class="btn" style="left:112px;top:1133px;width:152px;height:42px">Learn more <span class="arrow"></span></div>
  <div class="abs framed"><div class="photo" role="img" aria-label="Photo of a couple leaving the ceremony under a shower of confetti" style="position:relative;width:100%;height:100%;background:linear-gradient(135deg,#5a4a44,#8a7a70 50%,#4a3e3a)"><div class="play" style="left:190px;top:146px"></div></div></div>
</section>

<!-- Latest videos -->
<div class="abs band-latest"></div>
<h2 class="abs heading latest-title">Latest wedding videos</h2>
<div class="video-card" style="left:118px;background:linear-gradient(135deg,#4f4a52,#a08d8a 55%,#6a5f5a)" role="img" aria-label="Video still of a bride and groom kissing with guests behind"><div class="play" style="left:202px;top:139px"></div></div>
<div class="video-card" style="left:616px;background:linear-gradient(135deg,#3a3530,#7b6c60 50%,#c9c2bb)" role="img" aria-label="Video still of a groom leading his bride by the hand"><div class="play" style="left:202px;top:139px"></div></div>
<div class="dots" style="top:1823px"><i></i><i></i><i class="off"></i><i></i><i></i></div>

<!-- About -->
<div class="abs about-silhouette" role="img" aria-label="Soft grey silhouette of a couple about to kiss"></div>
<section class="about">
  <h2 class="abs heading">Bruno Lessway, a <span class="gold">trusted</span> and acclaimed wedding filmmaker<br>based in the <span class="gold">North East</span> and <span class="gold">Yorkshire</span>, has more than<br><span class="gold">20 years</span> of filmmaking experience</h2>
  <p class="abs">From beautiful barns and luxurious country hotels to sun-drenched Greek Islands and ancient Italian abbeys, he has filmed all kinds of unforgettable weddings. If you're looking for a highly experienced wedding videographer who focuses on your story, the goosebump moments and the emotions filling the room as you entertain your guests, then get in touch with Bruno today</p>
  <div class="btn" style="left:524px;top:2160px;width:152px;height:40px">Learn more <span class="arrow"></span></div>
</section>

<!-- Testimonials -->
<div class="abs testi" role="img" aria-label="Faded photo of a laughing bride in the background"></div>
<h2 class="abs heading testi-title">Testimonials</h2>
<article class="abs t-card" style="left:110px">
  <div class="round" role="img" aria-label="Photo of the couple Amara and Joel" style="background:linear-gradient(135deg,#8b7d70,#d8d0c6)"></div>
  <h3>AMARA + JOEL</h3>
  <p>"we Have A Really Emotional Video For Our Wedding. It Is A Beauty Video That Is Going To Stay With Us For The Rest Of Our Lives. Bruno Was Everywhere But You Couldn't Tell He Was There."</p>
  <div class="venue">MARRIED AT VILLA SERENA,<br>UMBRIA, ITALY</div>
</article>
<article class="abs t-card" style="left:612px">
  <div class="round" role="img" aria-label="Photo of the couple Hannah and Luca" style="background:linear-gradient(135deg,#3e3a3c,#bdb6b0)"></div>
  <h3>HANNAH + LUCA</h3>
  <p>We enjoyed the day so much but it was great to see how much our guests had enjoyed it too. The amount of shots of our friends and family arriving, chatting, enjoying the food</p>
  <div class="venue">MARRIED AT VILLA SERENA,<br>UMBRIA, ITALY</div>
</article>
<div class="dots" style="top:2725px"><i></i><i></i><i class="off"></i><i></i><i></i></div>

<!-- Packages -->
<div class="abs packs-bg" role="img" aria-label="Faded grey photo of a couple holding hands in a field"></div>
<h2 class="abs heading packs-title">Packages</h2>
<article class="abs pack" style="left:102px">
  <svg width="314" height="120"><polygon points="0,0 314,0 314,88 0,112" fill="#a48d4f"/></svg>
  <h3>WEDDING PHOTOGRAPHY</h3><div class="price">£700</div>
  <p>Add wedding photography onto your package. This includes coverage from 2.5 hours before the wedding ceremony to shortly after the first dance. A minimum of 700 photographs are provided on USB memory stick and as a digital download.</p>
  <div class="btn outline" style="left:92px;top:326px;width:130px;height:38px">Learn more <span class="arrow"></span></div>
</article>
<article class="abs pack" style="left:443px">
  <svg width="314" height="120"><polygon points="0,0 314,0 314,88 0,112" fill="#a48d4f"/></svg>
  <h3>LATE NIGHT FILMING</h3><div class="price">£200</div>
  <p>My normal coverage ends shortly after the first dance however I am available to stay until 10pm to capture more partying and antics. This is perfect to capture more guests dancing and often many funny moments.</p>
  <div class="btn outline" style="left:92px;top:326px;width:130px;height:38px">Learn more <span class="arrow"></span></div>
</article>
<article class="abs pack" style="left:783px">
  <svg width="314" height="120"><polygon points="0,0 314,0 314,88 0,112" fill="#a48d4f"/></svg>
  <h3>ENGAGEMENT FILM</h3><div class="price">£200</div>
  <p>A pre-wedding shoot is a great option to make a little film at a location you love before your wedding day. This option is available as a stand alone film before making a decision if you'd like to book me for your wedding video.</p>
  <div class="btn outline" style="left:92px;top:326px;width:130px;height:38px">Learn more <span class="arrow"></span></div>
</article>

<!-- Get in touch -->
<div class="abs touch"></div>
<h2 class="abs heading touch-title">Get in touch</h2>
<p class="abs touch-text">Bruno works with a limited number of couples every year, so if you're looking for a friendly, professional wedding filmmaker in the North East and Yorkshire region, who will exceed your expectations, take that first step today. Complete the enquiry form or take a look at more of Bruno's breathtaking wedding videos and 5* feedback on his Friendbook page.</p>
<div class="btn outline" style="left:413px;top:3699px;width:374px;height:46px;border-color:#fff">Download my wedding video brochure <span class="arrow"></span></div>

<!-- Footer -->
<footer class="abs footer"></footer>
<div class="abs f-head" style="left:117px">Quick links</div>
<ul class="abs f-links"><li>FAQ's</li><li>Wedding Photography</li><li>Commercial</li><li>North East Wedding Venues</li><li>Free Speeches Guide</li></ul>
<div class="abs f-head" style="left:388px">Contact us</div>
<div class="abs f-contact">
  <div class="f-row"><span class="ic"><svg width="12" height="16" viewBox="0 0 12 16"><path fill="#fff" d="M6 0a6 6 0 0 0-6 6c0 4.5 6 10 6 10s6-5.5 6-10a6 6 0 0 0-6-6zm0 8.5A2.5 2.5 0 1 1 6 3.5a2.5 2.5 0 0 1 0 5z"/></svg></span><span>PO Box 214 Ca 40217<br>United Kingdom</span></div>
  <div class="f-row"><span class="ic"><svg width="14" height="14" viewBox="0 0 24 24"><path fill="#fff" d="M6.6 10.8a15 15 0 0 0 6.6 6.6l2.2-2.2c.3-.3.7-.4 1-.2 1.1.4 2.3.6 3.6.6.6 0 1 .4 1 1V20c0 .6-.4 1-1 1A17 17 0 0 1 3 4c0-.6.4-1 1-1h3.5c.6 0 1 .4 1 1 0 1.3.2 2.5.6 3.6.1.3 0 .7-.2 1z"/></svg></span><span style="font-size:13px;font-weight:700">07700 900 123</span></div>
  <div class="f-row"><span class="ic"><svg width="14" height="11" viewBox="0 0 14 11"><path fill="#fff" d="M0 0h14v11H0zM1 1.2v.6l6 4 6-4v-.6z"/></svg></span><span style="font-size:13px">films@brunolessway.com</span></div>
</div>
<div class="abs f-head" style="left:643px">Follow on Snapgram</div>
<div class="abs grid" role="img" aria-label="Grid of six recent wedding photos"><i></i><i></i><i></i><i></i><i></i><i></i></div>
<div class="abs" style="left:940px;top:3968px;width:135px;text-align:center;font:400 12px 'Questrial',sans-serif;letter-spacing:2px;color:#fff">BRUNO LESSWAY</div>
<div class="abs" style="left:929px;top:4022px;width:52px;height:60px;background:#2c3e8f;border-radius:4px" role="img" aria-label="Certification badge"></div>
<div class="abs" style="left:1016px;top:4016px;width:70px;height:70px;border-radius:50%;background:#efe39a" role="img" aria-label="Listing badge"></div>
<div class="abs f-rule"></div>
<div class="abs copy">© 2022 Bruno Lessway. All Rights Reserved</div>

</body>
</html>
```